Architectural, Engineering and Design Build

Tovandex4.com
Veteran Disabled Certified company is doing business in Architecture, Engineer and Design build - look simialr websites and come up with design follow following website
https://hollis-darnet.example/
https://www.venlorcogroup.example/
https://www.pembrisgc.example/contract-vehicles/service-disabled-veteran-owned-small-business-sdvosb/
https://www.corbelnetlink.example/about/sdvosb/

Target Market(s)

US - Defense and Federal Government

Industry/Entity Type

Colors
0054AA
0677BA
7BADD7
CADEEF
E8F1F8

Requirements
Must have
• Army, American patriotism , Buildings, construction, architecture, engineering
Nice to have
• I need to attract federal government agencies and Defense

```html
<!DOCTYPE html>
<html lang="en">
<head>
<meta charset="utf-8">
<title>Tovandex4 – Homepage Concepts</title>
<link href="https://fonts.googleapis.com/css2?family=Michroma&family=Roboto:wght@400;500;700&display=swap" rel="stylesheet">
<style>
  :root{
    --navy:#17206a;
    --navy-deep:#121a58;
    --red:#e0141b;
    --stage:#f2f2f7;
    --soft:#f4f4f6;
    --ink:#222;
    --muted:#555;
    --white:#fff;
  }
  *{box-sizing:border-box;margin:0;padding:0}
  html,body{width:822px;height:1200px;overflow:hidden;background:var(--stage)}
  body{font-family:"Roboto",Arial,sans-serif;color:var(--ink)}
  .board{position:absolute;left:0;top:0;width:1591px;height:2324px;transform:scale(.51666);transform-origin:0 0}
  .page{position:absolute;top:90px;width:661px;height:2144px;background:var(--white);overflow:hidden;box-shadow:0 0 30px rgba(20,30,90,.06)}
  .page--a{left:96px}
  .page--b{left:834px}
  .abs{position:absolute}
  .display{font-family:"Michroma",Arial,sans-serif;color:var(--navy);letter-spacing:4px;line-height:1;white-space:nowrap}
  .eyebrow{font-size:9px;font-weight:500;color:var(--red);text-transform:uppercase;line-height:1}
  .btn{position:absolute;display:flex;align-items:center;justify-content:center;font-size:8.5px;font-weight:700;text-transform:uppercase;background:var(--red);color:var(--white)}
  .btn--ghost{background:var(--white);color:var(--navy-deep);border:1px solid var(--red)}
  .rule{position:absolute;height:1.5px;width:22px;background:var(--red)}

  /* top bar */
  .topbar{left:0;top:0;width:661px;height:28px;background:var(--navy)}
  .topbar__red{left:0;top:0;width:661px;height:28px;background:var(--red);clip-path:polygon(532px 0,661px 0,661px 28px,505px 28px)}
  .topbar__item{top:10px;font-family:"Michroma",Arial,sans-serif;font-size:6.5px;line-height:1;color:var(--white);letter-spacing:1px;display:flex;align-items:center;gap:6px;white-space:nowrap}
  .topbar__sep{top:8px;left:187px;width:1px;height:11px;background:var(--white)}
  .social{position:absolute;display:flex;gap:6px}
  .social span{width:16px;height:16px;display:block;background:var(--white);border:1px solid var(--white)}
  .social--top{left:538px;top:6px}

  /* header */
  .header{left:0;top:28px;width:661px;height:68px;background:var(--white)}
  .brand{display:flex;align-items:center;gap:5px;font-weight:700;font-size:13px;color:var(--navy)}
  .brand i{width:14px;height:14px;border-radius:50%;background:var(--red);display:block}
  .header .brand{position:absolute;left:62px;top:26px}
  .nav{position:absolute;top:31px;display:flex;gap:30px;font-size:9.5px;font-weight:500;color:var(--ink);text-transform:uppercase;white-space:nowrap}
  .nav .is-active{color:var(--red)}
  .header .nav{left:252px}

  /* hero */
  .hero{left:0;top:96px;width:661px;height:316px;background:linear-gradient(90deg,#e9e9ea 0%,#e4e4e6 45%,#d6d7da 100%)}
  .hero__photo{position:absolute;top:0;bottom:0}
  .hero__title{left:62px;top:187px;font-size:23px;letter-spacing:5px}
  .hero__tag{left:62px;top:220px;font-size:16px;letter-spacing:4px}
  .hero__text{left:62px;top:249px;width:300px;font-size:11.5px;line-height:16px;color:var(--ink)}
  .hero__dots{left:306px;top:386px;display:flex;align-items:center;gap:9px}
  .hero__dots span{width:3px;height:3px;border-radius:50%;background:var(--navy)}
  .hero__dots .on{width:11px;height:11px;border:2px solid var(--white);background:var(--red);box-shadow:0 0 0 1px var(--red)}

  /* about */
  .about__img1{left:62px;top:478px;width:254px;height:236px;background:linear-gradient(160deg,#b9c6d4 0%,#9a8e7a 55%,#7b7164 100%)}
  .about__img2{left:193px;top:609px;width:160px;height:140px;border:4px solid var(--white);background:linear-gradient(160deg,#90a8c4 0%,#6e7b85 50%,#3e3f48 100%)}
  .about__title{left:400px;top:503px;font-size:17px}
  .copy{font-size:8.5px;line-height:14.2px;color:var(--muted);text-align:justify}

  /* services */
  .services__band{left:0;top:822px;width:661px;height:281px;background:radial-gradient(circle at 15% 20%,#f0343a 0%,#e0141b 40%,#d10f16 100%)}
  .center{left:0;width:661px;text-align:center}
  .services__title{top:886px;font-size:17px;color:var(--white)}
  .services__text{left:80px;top:918px;width:501px;text-align:center;font-size:8.2px;line-height:14.2px;font-weight:500;color:var(--white)}
  .card{position:absolute;top:979px;width:167px;height:261px;background:var(--white);box-shadow:0 2px 8px rgba(0,0,0,.12)}
  .card__img{position:absolute;left:4px;top:4px;width:159px;height:119px}
  .card__title{position:absolute;left:0;top:136px;width:167px;text-align:center;font-size:9px;font-weight:500;color:var(--navy-deep);text-transform:uppercase;line-height:1}
  .card__dot{position:absolute;left:81px;top:150px;width:4px;height:4px;border-radius:50%;background:var(--red)}
  .card__text{position:absolute;left:10px;top:160px;width:147px;text-align:center;font-size:8.3px;line-height:14.2px;color:var(--ink)}
  .card .btn{left:49px;top:225px;width:69px;height:23px;font-size:7px}

  /* projects */
  .projects__title{top:1317px;font-size:17px}
  .tile{position:absolute}
  .tile--hover{background:linear-gradient(rgba(30,40,140,.85),rgba(30,40,140,.85)),linear-gradient(160deg,#7b86a8,#4a5378);border:2px solid var(--red)}

  /* contact */
  .contact{left:0;top:1730px;width:661px;height:264px;background:var(--soft)}
  .contact__title{top:1787px;font-size:17px}
  .field{position:absolute;background:var(--white);font-size:8px;color:#555;padding:10px 10px}

  /* footer */
  .footer{left:0;top:1994px;width:661px;height:150px;background:linear-gradient(120deg,#17206a 0%,#1b2678 55%,#141c60 100%)}
  .footer .brand{position:absolute;left:62px;top:58px;color:var(--white)}
  .footer .nav{left:252px;top:37px;color:var(--white);font-size:9.5px}
  .footer__contact{top:57px}
  .footer .social{left:538px;top:74px}
  .footer .social span{background:transparent;border:1px solid var(--white)}
  .footer .social span:first-child{background:var(--red);border-color:var(--red)}
  .footer__rule{left:62px;top:113px;width:537px;height:1px;background:rgba(255,255,255,.2)}
  .footer__copy{left:0;width:661px;top:125px;text-align:center;font-size:7.5px;font-weight:500;color:var(--white)}
</style>
</head>
<body>
<div class="board">

  <section class="page page--a">
    <div class="abs topbar"></div>
    <div class="abs topbar__red"></div>
    <div class="abs topbar__item" style="left:62px"><svg width="7" height="7" viewBox="0 0 10 10"><path d="M2 0l2 2-1 2 3 3 2-1 2 2-2 2C4 10 0 6 0 2z" fill="#e0141b"/></svg>+1 (555) 014 2290</div>
    <div class="abs topbar__sep"></div>
    <div class="abs topbar__item" style="left:206px"><svg width="8" height="6" viewBox="0 0 10 7"><rect width="10" height="7" fill="#e0141b"/><path d="M0 0l5 4 5-4" stroke="#fff" fill="none"/></svg>info@tovandex4.com</div>
    <div class="social social--top"><span></span><span></span><span></span></div>

    <header class="abs header">
      <div class="brand"><i></i>TOVANDEX4</div>
      <nav class="nav"><span class="is-active">Home</span><span>About Us</span><span>Our Services</span><span>Blog</span><span>Contact Us</span></nav>
    </header>

    <div class="abs hero">
      <div class="hero__photo" role="img" aria-label="Builder holding a hard hat with a city skyline and crane blended in" style="left:330px;right:0;background:linear-gradient(100deg,rgba(230,230,232,0) 0%,#b7bcc4 30%,#8e98a8 55%,#c9a34a 70%,#e8e6e2 100%)"></div>
    </div>
    <h1 class="abs display hero__title">TOVANDEX4</h1>
    <p class="abs display hero__tag">WHATEVER IT TAKES</p>
    <p class="abs hero__text">Lorem ipsum dolor sit amet, consectetur adipiscing elit sed do eiusmod incididunt ut laborea.</p>
    <div class="btn" style="left:62px;top:298px;width:85px;height:28px">Get Started</div>
    <div class="abs hero__dots"><span></span><span class="on"></span><span></span><span></span></div>

    <div class="abs about__img1" role="img" aria-label="Construction crew in safety vests in front of a building under construction"></div>
    <div class="abs about__img2" role="img" aria-label="Engineers reviewing plans on a construction site"></div>
    <p class="abs eyebrow" style="left:400px;top:488px">Who We Are</p>
    <h2 class="abs display about__title">ABOUT US</h2>
    <div class="rule" style="left:383px;top:527px"></div>
    <p class="abs copy" style="left:400px;top:541px;width:200px">Lorem ipsum dolor sit amet, consectetur adipiscing elit, sed do eiusmod tempor incididunt ut labore et dolore magna aliqua. Ut enim ad minim veniam, quis nostrud exercitation ullamco laboris nisi ut aliquip ex ea commodo consequat. Duis aute irure dolor in reprehenderit in voluptate velit esse cillum dolore eu fugiat nulla pariatur.</p>
    <p class="abs copy" style="left:400px;top:650px;width:200px">Lorem ipsum dolor sit amet, consectetur adipiscing elit, sed do eiusmod tempor incididunt ut labore et dolore magna aliquea.</p>
    <div class="btn" style="left:400px;top:709px;width:81px;height:28px">Learn More</div>

    <div class="abs services__band" role="img" aria-label="Red field with faint eagle and star decoration"></div>
    <p class="abs eyebrow center" style="top:871px;color:#fff">What We Do</p>
    <h2 class="abs display center services__title">OUR SERVICES</h2>
    <p class="abs services__text">Lorem ipsum dolor sit amet, consectetur adipiscing elit, sed do eiusmod tempor incididunt ut labore et dolore magna aliqua. Ut enim ad minim veniam, quis nostrud exercitation ullamco laboris nisi ut aliquip ex ea commodo consequat. Duis aute irure dolor in reprehenderit in voluptate velit esse cillum dolore eu fugiat nulla pariature.</p>
    <article class="card" style="left:62px">
      <div class="card__img" role="img" aria-label="Modern white house over architectural drawings" style="background:linear-gradient(160deg,#e6e9ec,#b9bdc2 60%,#8e9296)"></div>
      <h3 class="card__title">Architecture</h3><i class="card__dot"></i>
      <p class="card__text">Lorem ipsum dolor sit amet, consec adipiscing elit, sed do eiusmod tempor incididunt ut laboreet dolor magna aliqua.</p>
      <div class="btn btn--ghost">Learn More</div>
    </article>
    <article class="card" style="left:247px">
      <div class="card__img" role="img" aria-label="Engineers in hard hats on a site at sunset" style="background:linear-gradient(160deg,#6f8fc4,#c99a6a 55%,#3f4a66)"></div>
      <h3 class="card__title">Engineering</h3><i class="card__dot"></i>
      <p class="card__text">Lorem ipsum dolor sit amet, consec adipiscing elit, sed do eiusmod tempor incididunt ut laboreet dolor magna aliqua.</p>
      <div class="btn">Learn More</div>
    </article>
    <article class="card" style="left:432px">
      <div class="card__img" role="img" aria-label="Glass office building design rendering" style="background:linear-gradient(160deg,#f0f1f2,#bfc6cc 55%,#8a949c)"></div>
      <h3 class="card__title">Design Build</h3><i class="card__dot"></i>
      <p class="card__text">Lorem ipsum dolor sit amet, consec adipiscing elit, sed do eiusmod tempor incididunt ut laboreet dolor magna aliqua.</p>
      <div class="btn btn--ghost">Learn More</div>
    </article>

    <p class="abs eyebrow center" style="top:1302px">Gallery</p>
    <h2 class="abs display center projects__title">OUR PROJECTS</h2>
    <div class="rule" style="left:320px;top:1338px"></div>
    <div class="tile" role="img" aria-label="Houses with timber frames under construction" style="left:62px;top:1363px;width:264px;height:155px;background:linear-gradient(170deg,#8fb0cf,#d9c7a4 45%,#8a6f55)"></div>
    <div class="tile" role="img" aria-label="High-rise concrete frame with crane and skyline" style="left:335px;top:1363px;width:264px;height:155px;background:linear-gradient(170deg,#e6d9c4,#c9b89d 50%,#4e4233)"></div>
    <div class="tile" role="img" aria-label="Tower crane beside a white building" style="left:62px;top:1527px;width:173px;height:127px;background:linear-gradient(160deg,#4f8fd0,#a8c8e8 45%,#c9c9c6)"></div>
    <div class="tile tile--hover" role="img" aria-label="Apartment building highlighted with view icon" style="left:244px;top:1527px;width:173px;height:127px"><svg class="abs" style="left:79px;top:56px" width="14" height="14" viewBox="0 0 14 14"><circle cx="6" cy="6" r="4.5" stroke="#fff" stroke-width="1.5" fill="none"/><path d="M9.5 9.5L13 13M6 4v4M4 6h4" stroke="#fff" stroke-width="1.5"/></svg></div>
    <div class="tile" role="img" aria-label="Modern house rendering over drawings" style="left:426px;top:1527px;width:173px;height:127px;background:linear-gradient(160deg,#c8d8e8,#9a9a98 50%,#b56a3e 70%,#e2e2e0)"></div>

    <div class="abs contact"></div>
    <p class="abs eyebrow center" style="top:1772px">Contact Us</p>
    <h2 class="abs display center contact__title">GET IN TOUCH</h2>
    <div class="rule" style="left:320px;top:1808px"></div>
    <div class="field" style="left:91px;top:1830px;width:155px;height:26px">Full Name</div>
    <div class="field" style="left:252px;top:1830px;width:156px;height:26px">Phone</div>
    <div class="field" style="left:414px;top:1830px;width:155px;height:26px">Email Address</div>
    <div class="field" style="left:91px;top:1864px;width:478px;height:50px">Message</div>
    <div class="btn" style="left:286px;top:1924px;width:89px;height:26px">Send Message</div>

    <footer class="abs footer">
      <div class="brand"><i></i>TOVANDEX4</div>
      <nav class="nav"><span>Home</span><span>About Us</span><span>Our Services</span><span>Blog</span><span>Contact Us</span></nav>
      <div class="abs topbar__item footer__contact" style="left:333px"><svg width="7" height="7" viewBox="0 0 10 10"><path d="M2 0l2 2-1 2 3 3 2-1 2 2-2 2C4 10 0 6 0 2z" fill="#e0141b"/></svg>+1 (555) 014 2290</div>
      <div class="abs" style="left:467px;top:55px;width:1px;height:11px;background:#fff"></div>
      <div class="abs topbar__item footer__contact" style="left:486px"><svg width="8" height="6" viewBox="0 0 10 7"><rect width="10" height="7" fill="#e0141b"/><path d="M0 0l5 4 5-4" stroke="#fff" fill="none"/></svg>info@tovandex4.com</div>
      <div class="social"><span></span><span></span><span></span></div>
      <div class="abs footer__rule"></div>
      <p class="abs footer__copy">Copyright © 2024 / All Rights Reserved</p>
    </footer>
  </section>

  <section class="page page--b">
    <div class="abs topbar"></div>
    <div class="abs topbar__red"></div>
    <div class="abs topbar__item" style="left:62px"><svg width="7" height="7" viewBox="0 0 10 10"><path d="M2 0l2 2-1 2 3 3 2-1 2 2-2 2C4 10 0 6 0 2z" fill="#e0141b"/></svg>+1 (555) 014 2290</div>
    <div class="abs topbar__sep"></div>
    <div class="abs topbar__item" style="left:206px"><svg width="8" height="6" viewBox="0 0 10 7"><rect width="10" height="7" fill="#e0141b"/><path d="M0 0l5 4 5-4" stroke="#fff" fill="none"/></svg>info@tovandex4.com</div>
    <div class="social social--top"><span></span><span></span><span></span></div>

    <header class="abs header">
      <div class="brand"><i></i>TOVANDEX4</div>
      <nav class="nav"><span class="is-active">Home</span><span>About Us</span><span>Our Services</span><span>Blog</span><span>Contact Us</span></nav>
    </header>

    <div class="abs hero">
      <div class="hero__photo" role="img" aria-label="Construction worker in hard hat blended with a city skyline" style="left:0;right:0;background:linear-gradient(90deg,#dfe1e6 0%,#d2d5db 35%,#b4a79a 55%,#e8a868 62%,#a9aeb6 78%,#cfd2d8 100%)"></div>
    </div>
    <h1 class="abs display hero__title">TOVANDEX4</h1>
    <p class="abs display hero__tag">WHATEVER IT TAKES</p>
    <p class="abs hero__text">Lorem ipsum dolor sit amet, consectetur adipiscing elit sed do eiusmod incididunt ut laborea.</p>
    <div class="btn" style="left:62px;top:298px;width:85px;height:28px">Get Started</div>
    <div class="abs hero__dots"><span></span><span class="on"></span><span></span><span></span></div>

    <div class="abs about__img1" role="img" aria-label="Construction crew in safety vests in front of a building under construction"></div>
    <div class="abs about__img2" role="img" aria-label="Engineers reviewing plans on a construction site"></div>
    <p class="abs eyebrow" style="left:400px;top:488px">Who We Are</p>
    <h2 class="abs display about__title">ABOUT US</h2>
    <div class="rule" style="left:383px;top:527px"></div>
    <p class="abs copy" style="left:400px;top:541px;width:200px">Lorem ipsum dolor sit amet, consectetur adipiscing elit, sed do eiusmod tempor incididunt ut labore et dolore magna aliqua. Ut enim ad minim veniam, quis nostrud exercitation ullamco laboris nisi ut aliquip ex ea commodo consequat. Duis aute irure dolor in reprehenderit in voluptate velit esse cillum dolore eu fugiat nulla pariatur.</p>
    <p class="abs copy" style="left:400px;top:650px;width:200px">Lorem ipsum dolor sit amet, consectetur adipiscing elit, sed do eiusmod tempor incididunt ut labore et dolore magna aliquea.</p>
    <div class="btn" style="left:400px;top:709px;width:81px;height:28px">Learn More</div>

    <div class="abs services__band" role="img" aria-label="Red field with faint eagle and star decoration"></div>
    <p class="abs eyebrow center" style="top:871px;color:#fff">What We Do</p>
    <h2 class="abs display center services__title">OUR SERVICES</h2>
    <p class="abs services__text">Lorem ipsum dolor sit amet, consectetur adipiscing elit, sed do eiusmod tempor incididunt ut labore et dolore magna aliqua. Ut enim ad minim veniam, quis nostrud exercitation ullamco laboris nisi ut aliquip ex ea commodo consequat. Duis aute irure dolor in reprehenderit in voluptate velit esse cillum dolore eu fugiat nulla pariature.</p>
    <article class="card" style="left:62px">
      <div class="card__img" role="img" aria-label="Modern white house over architectural drawings" style="background:linear-gradient(160deg,#e6e9ec,#b9bdc2 60%,#8e9296)"></div>
      <h3 class="card__title">Architecture</h3><i class="card__dot"></i>
      <p class="card__text">Lorem ipsum dolor sit amet, consec adipiscing elit, sed do eiusmod tempor incididunt ut laboreet dolor magna aliqua.</p>
      <div class="btn btn--ghost">Learn More</div>
    </article>
    <article class="card" style="left:247px">
      <div class="card__img" role="img" aria-label="Engineers in hard hats on a site at sunset" style="background:linear-gradient(160deg,#6f8fc4,#c99a6a 55%,#3f4a66)"></div>
      <h3 class="card__title">Engineering</h3><i class="card__dot"></i>
      <p class="card__text">Lorem ipsum dolor sit amet, consec adipiscing elit, sed do eiusmod tempor incididunt ut laboreet dolor magna aliqua.</p>
      <div class="btn">Learn More</div>
    </article>
    <article class="card" style="left:432px">
      <div class="card__img" role="img" aria-label="Glass office building design rendering" style="background:linear-gradient(160deg,#f0f1f2,#bfc6cc 55%,#8a949c)"></div>
      <h3 class="card__title">Design Build</h3><i class="card__dot"></i>
      <p class="card__text">Lorem ipsum dolor sit amet, consec adipiscing elit, sed do eiusmod tempor incididunt ut laboreet dolor magna aliqua.</p>
      <div class="btn btn--ghost">Learn More</div>
    </article>

    <p class="abs eyebrow center" style="top:1302px">Gallery</p>
    <h2 class="abs display center projects__title">OUR PROJECTS</h2>
    <div class="rule" style="left:320px;top:1338px"></div>
    <div class="tile" role="img" aria-label="Houses with timber frames under construction" style="left:62px;top:1363px;width:264px;height:155px;background:linear-gradient(170deg,#8fb0cf,#d9c7a4 45%,#8a6f55)"></div>
    <div class="tile" role="img" aria-label="High-rise concrete frame with crane and skyline" style="left:335px;top:1363px;width:264px;height:155px;background:linear-gradient(170deg,#e6d9c4,#c9b89d 50%,#4e4233)"></div>
    <div class="tile" role="img" aria-label="Tower crane beside a white building" style="left:62px;top:1527px;width:173px;height:127px;background:linear-gradient(160deg,#4f8fd0,#a8c8e8 45%,#c9c9c6)"></div>
    <div class="tile tile--hover" role="img" aria-label="Apartment building highlighted with view icon" style="left:244px;top:1527px;width:173px;height:127px"><svg class="abs" style="left:79px;top:56px" width="14" height="14" viewBox="0 0 14 14"><circle cx="6" cy="6" r="4.5" stroke="#fff" stroke-width="1.5" fill="none"/><path d="M9.5 9.5L13 13M6 4v4M4 6h4" stroke="#fff" stroke-width="1.5"/></svg></div>
    <div class="tile" role="img" aria-label="Modern house rendering over drawings" style="left:426px;top:1527px;width:173px;height:127px;background:linear-gradient(160deg,#c8d8e8,#9a9a98 50%,#b56a3e 70%,#e2e2e0)"></div>

    <div class="abs contact"></div>
    <p class="abs eyebrow center" style="top:1772px">Contact Us</p>
    <h2 class="abs display center contact__title">GET IN TOUCH</h2>
    <div class="rule" style="left:320px;top:1808px"></div>
    <div class="field" style="left:91px;top:1830px;width:155px;height:26px">Full Name</div>
    <div class="field" style="left:252px;top:1830px;width:156px;height:26px">Phone</div>
    <div class="field" style="left:414px;top:1830px;width:155px;height:26px">Email Address</div>
    <div class="field" style="left:91px;top:1864px;width:478px;height:50px">Message</div>
    <div class="btn" style="left:286px;top:1924px;width:89px;height:26px">Send Message</div>

    <footer class="abs footer">
      <div class="brand"><i></i>TOVANDEX4</div>
      <nav class="nav"><span>Home</span><span>About Us</span><span>Our Services</span><span>Blog</span><span>Contact Us</span></nav>
      <div class="abs topbar__item footer__contact" style="left:333px"><svg width="7" height="7" viewBox="0 0 10 10"><path d="M2 0l2 2-1 2 3 3 2-1 2 2-2 2C4 10 0 6 0 2z" fill="#e0141b"/></svg>+1 (555) 014 2290</div>
      <div class="abs" style="left:467px;top:55px;width:1px;height:11px;background:#fff"></div>
      <div class="abs topbar__item footer__contact" style="left:486px"><svg width="8" height="6" viewBox="0 0 10 7"><rect width="10" height="7" fill="#e0141b"/><path d="M0 0l5 4 5-4" stroke="#fff" fill="none"/></svg>info@tovandex4.com</div>
      <div class="social"><span></span><span></span><span></span></div>
      <div class="abs footer__rule"></div>
      <p class="abs footer__copy">Copyright © 2024 / All Rights Reserved</p>
    </footer>
  </section>

</div>
</body>
</html>
```